Casino with the 'highest winning percentage' needs a stationery design

This is for a casino in Colombo, Sri Lanka and we need a stationery design for business card, letter head and envelope.

Should be very professional, simple and elegant without fancy fonts

Reason: Not fully satisfied with the designs. Need more designs.

Business

• 1. card deck symbol 'CLUBS' in red, or black

2. name in BLOCK CAPITAL LETTERS

3. Preferred font colours are black, white or red

4. Prefer 'professional /elegant' fonts
• SHOULD NOT HAVE ANY OTHER SYMBOL EXCEPT 'CLUBS'

DO NOT PREFER ITALIC FONTS

```html
<!DOCTYPE html>
<html lang="en">
<head>
<meta charset="utf-8">
<title>Crestmoor Entertainment – Business Card</title>
<link rel="stylesheet" href="https://fonts.googleapis.com/css2?family=Noto+Serif:wght@400;700&display=swap">
<style>
  :root {
    --backdrop: #e8e3dc;
    --paper: #ffffff;
    --ink: #0d0d0d;
    --brand-red: #e01a45;
    --back-red: #e10f26;
    --on-red: #ffffff;
    --edge: #b9b2a8;
  }
  * { margin: 0; padding: 0; box-sizing: border-box; }
  html, body {
    width: 1200px; height: 1091px; overflow: hidden;
    background: var(--backdrop);
    font-family: "Noto Serif", Georgia, serif;
  }
  .stage { position: relative; width: 1200px; height: 1091px; }

  .card {
    position: absolute; width: 860px; height: 491px; overflow: hidden;
  }
  .card--front { left: 44px; top: 41px; background: var(--paper); border: 1px solid var(--edge); }
  .card--back { left: 302px; top: 561px; background: var(--back-red); }

  .brand-mark {
    position: absolute; border-radius: 50%;
  }
  .card--front .brand-mark { left: 72px; top: 86px; width: 118px; height: 118px; background: var(--brand-red); }
  .card--back .brand-mark { left: 168px; top: 200px; width: 104px; height: 104px; background: var(--on-red); }

  .brand-name {
    position: absolute; font-weight: 700; font-size: 49px; line-height: 60px; letter-spacing: 0.5px;
  }
  .card--front .brand-name { left: 236px; top: 86px; color: var(--ink); }
  .card--back .brand-name { left: 302px; top: 182px; color: var(--on-red); }

  .company {
    position: absolute; left: 56px; top: 278px;
    font-weight: 700; font-size: 26px; color: var(--brand-red); letter-spacing: 0.3px;
  }
  .address {
    position: absolute; left: 56px; top: 330px;
    font-size: 19.5px; line-height: 28px; color: var(--ink);
  }

  .swoosh { position: absolute; left: 0; top: 0; width: 860px; height: 491px; }

  .contacts {
    position: absolute; right: 13px; top: 323px; list-style: none;
    color: var(--on-red); font-size: 20px; line-height: 32px; text-align: right;
  }
  .contacts li { display: flex; justify-content: flex-end; align-items: center; gap: 9px; }
  .contacts svg { width: 16px; height: 16px; fill: var(--on-red); flex: none; }

  .tagline {
    position: absolute; left: 0; right: 0; top: 372px; text-align: center;
    font-weight: 700; font-size: 25px; letter-spacing: 2.4px; color: var(--on-red);
  }
</style>
</head>
<body>
<main class="stage">

  <section class="card card--front" aria-label="Business card front">
    <svg class="swoosh" viewBox="0 0 860 491" aria-hidden="true">
      <path d="M0,442 C150,505 380,500 545,398 C665,322 765,292 860,287 L860,491 L0,491 Z" fill="var(--brand-red)"/>
      <path d="M0,386 C140,462 380,472 540,370 C670,288 780,262 860,260 L860,275 C770,280 662,314 548,390 C402,482 160,492 0,420 Z" fill="var(--ink)"/>
      <path d="M75,404 C200,462 380,470 500,418 C380,452 220,448 75,404 Z" fill="var(--ink)"/>
    </svg>

    <div class="brand-mark" aria-hidden="true"></div>
    <h1 class="brand-name">CRESTMOOR<br>ENTERTAINMENT</h1>

    <p class="company">CRESTMOOR LIMITED</p>
    <p class="address">18, Lotus Grove Mawatha<br>Colombo 01000, Sri Lanka</p>

    <ul class="contacts">
      <li><svg viewBox="0 0 16 16"><path d="M3.5 1.5l2.5 0 1 3.5-1.8 1.2a8 8 0 0 0 4.6 4.6L11 9l3.5 1v2.5c0 1-1 2-2 2C6.5 14.5 1.5 9.5 1.5 3.5c0-1 1-2 2-2z"/></svg>+94 11 2450876</li>
      <li><svg viewBox="0 0 16 16"><path d="M4.5 0.5h7a1 1 0 0 1 1 1v13a1 1 0 0 1-1 1h-7a1 1 0 0 1-1-1v-13a1 1 0 0 1 1-1zM5 2.5v8h6v-8zM7 12v1.5h2V12z"/></svg>+94 77 5550142</li>
      <li><svg viewBox="0 0 16 16"><path d="M4 6l1.5-4h5L12 6h1.5a1 1 0 0 1 1 1v4.5h-1.5v2h-2v-2h-6v2H3v-2H1.5V7a1 1 0 0 1 1-1zM5.3 6h5.4l-1-2.5H6.3zM3 8v1.6h2V8zm8 0v1.6h2V8z"/></svg>+94 11 5550199</li>
      <li><svg viewBox="0 0 16 16"><path d="M1 6l7-4.5L15 6v8H1zM2.5 6.6L8 10l5.5-3.4L8 3.3z"/></svg>info@crestmoorcolombo.com</li>
      <li><svg viewBox="0 0 16 16"><path d="M8 1a7 7 0 1 0 0 14A7 7 0 0 0 8 1zm0 1.4c.9 0 1.8 1.8 2 4.6H6c.2-2.8 1.1-4.6 2-4.6zM2.5 7.1h2.3c.1-1.6.4-3 .9-4a5.6 5.6 0 0 0-3.2 4zm8.7 0h2.3a5.6 5.6 0 0 0-3.2-4c.5 1 .8 2.4.9 4zM2.5 8.9a5.6 5.6 0 0 0 3.2 4c-.5-1-.8-2.4-.9-4zm3.5 0c.2 2.8 1.1 4.7 2 4.7s1.8-1.9 2-4.7zm5.2 0c-.1 1.6-.4 3-.9 4a5.6 5.6 0 0 0 3.2-4z"/></svg>www.crestmoorcolombo.com</li>
    </ul>
  </section>

  <section class="card card--back" aria-label="Business card back">
    <div class="brand-mark" aria-hidden="true"></div>
    <h2 class="brand-name">CRESTMOOR<br>ENTERTAINMENT</h2>
    <p class="tagline">Highest Winning Percentage In The World</p>
  </section>

</main>
</body>
</html>
```